Business card for medical clinic

I need an upmarket, modern medical/health business card for my clinic

Contact Information for Business Card

name, address, email, qr code

```html
<!DOCTYPE html>
<html lang="en">
<head>
<meta charset="utf-8">
<title>Meridale Health Group – Business Card</title>
<link rel="stylesheet" href="https://fonts.googleapis.com/css2?family=Poppins:wght@400;500;600;700&display=swap">
<style>
  :root {
    --stage: #2a2e33;
    --card-white: #ffffff;
    --card-dark: #1b1c1f;
    --card-dark-soft: #2c2d31;
    --brand-blue: #1e8fd5;
    --brand-navy: #1f4f82;
    --ink: #141414;
    --muted-grey: #a9abb0;
  }
  * { box-sizing: border-box; margin: 0; padding: 0; }
  html, body { width: 1200px; height: 780px; overflow: hidden; }
  body {
    background: var(--stage);
    font-family: "Poppins", sans-serif;
    position: relative;
  }
  .card {
    position: absolute;
    top: 236px;
    width: 540px;
    height: 309px;
    border-radius: 4px;
    overflow: hidden;
    box-shadow: 0 14px 30px rgba(0,0,0,0.35);
  }
  .card--front { left: 40px; background: var(--card-white); }
  .card--back  { left: 620px; background: var(--card-dark); }

  /* front */
  .brand {
    position: absolute;
    left: 34px; top: 46px;
    display: flex; align-items: center; gap: 10px;
  }
  .brand__circle {
    width: 34px; height: 34px;
    border: 3px solid var(--brand-navy);
    border-radius: 50%;
  }
  .brand__name {
    font-weight: 600;
    font-size: 17px;
    letter-spacing: 1.5px;
    color: var(--brand-navy);
    text-transform: uppercase;
  }
  .divider {
    position: absolute;
    left: 0; top: 0;
    width: 540px; height: 309px;
  }
  .person {
    position: absolute;
    left: 298px; top: 100px;
    width: 220px;
  }
  .person__name {
    font-size: 26px;
    line-height: 1.1;
    color: var(--brand-blue);
    white-space: nowrap;
  }
  .person__first { font-weight: 700; }
  .person__last { font-weight: 400; }
  .person__role {
    font-weight: 600;
    font-size: 14px;
    color: var(--ink);
    margin-top: 2px;
  }
  .contact {
    list-style: none;
    margin-top: 12px;
  }
  .contact__item {
    display: flex; align-items: center; gap: 8px;
    font-size: 13px;
    color: var(--ink);
    line-height: 22px;
    white-space: nowrap;
  }
  .contact__icon { width: 13px; height: 13px; flex: none; }
  .address {
    position: absolute;
    left: 34px; bottom: 26px;
    font-size: 14px;
    color: var(--brand-blue);
  }

  /* back */
  .back-pattern {
    position: absolute; inset: 0;
    background: radial-gradient(ellipse at 85% 20%, #4a4b50 0%, var(--card-dark-soft) 40%, var(--card-dark) 80%);
  }
  .back-brand {
    position: absolute;
    left: 50%; top: 62%;
    transform: translate(-50%, -50%);
    display: flex; align-items: center; gap: 6px;
  }
  .back-brand__circle {
    width: 14px; height: 14px;
    border: 1.5px solid var(--muted-grey);
    border-radius: 50%;
  }
  .back-brand__name {
    font-weight: 600;
    font-size: 8px;
    letter-spacing: 1px;
    color: var(--muted-grey);
    text-transform: uppercase;
  }
</style>
</head>
<body>
  <section class="card card--front">
    <div class="brand">
      <span class="brand__circle"></span>
      <span class="brand__name">Meridale Health Group</span>
    </div>

    <svg class="divider" viewBox="0 0 540 309" aria-hidden="true">
      <line x1="190" y1="248" x2="284" y2="96" stroke="#1e8fd5" stroke-width="1"/>
    </svg>

    <div class="person">
      <h1 class="person__name"><span class="person__first">Marta</span> <span class="person__last">Kovenska</span></h1>
      <p class="person__role">Founder &amp; CEO</p>
      <ul class="contact">
        <li class="contact__item">
          <svg class="contact__icon" viewBox="0 0 16 16" aria-hidden="true"><path d="M4 1.5l2.3 3-1.4 1.6c.8 1.9 2.2 3.3 4 4.1l1.6-1.4 3 2.3-1.3 2.6C7 13.3 2.7 9 1.4 2.8z" fill="#1e8fd5"/></svg>
          <span>(555) 204-6187</span>
        </li>
        <li class="contact__item">
          <svg class="contact__icon" viewBox="0 0 16 16" aria-hidden="true"><rect x="1" y="3" width="14" height="10" rx="1.5" fill="#1e8fd5"/><path d="M1.5 4l6.5 5 6.5-5" stroke="#fff" stroke-width="1.3" fill="none"/></svg>
          <span>hello@meridalehealth.com</span>
        </li>
        <li class="contact__item">
          <svg class="contact__icon" viewBox="0 0 16 16" aria-hidden="true"><circle cx="8" cy="8" r="7" fill="#1e8fd5"/><path d="M1 8h14M8 1c-3 3.5-3 10.5 0 14M8 1c3 3.5 3 10.5 0 14" stroke="#fff" stroke-width="1" fill="none"/></svg>
          <span>www.meridalehealth.com</span>
        </li>
      </ul>
    </div>

    <p class="address">418 Linden Park Ave. Suite 310 Ashford, TX 75990</p>
  </section>

  <section class="card card--back">
    <div class="back-pattern" role="img" aria-label="Embossed repeating pattern of the brand symbol on a dark background"></div>
    <div class="back-brand">
      <span class="back-brand__circle"></span>
      <span class="back-brand__name">Meridale Health Group</span>
    </div>
  </section>
</body>
</html>
```